Help us stand out from the crowd - Court of Maywell

We are a luxury watch business and are looking to develop our own paperwork that we can issue with our watches etc. I am looking for the following documents to be designed: Invoice, Warranty card, Insurance valuation, instruction booklet and a small folder to keep it all in. Need it to be small though. I have attached some images of my friends ones that look fantastic.

Target Market(s)

High net worth watch enthusiasts

Requirements
Must have
• Must be clean, precise and very easy on the eye. Think Vornel but underpinned with a classic british feel.
Should not have
• Shouldn't be dark.

```html
<!DOCTYPE html>
<html lang="en">
<head>
<meta charset="utf-8">
<title>Court of Maywell – Guarantee Card</title>
<link rel="stylesheet" href="https://fonts.googleapis.com/css2?family=Outfit:wght@300;400&display=swap">
<style>
  :root {
    --backdrop: #5d5d5d;
    --card: #ffffff;
    --ink: #1a1a1a;
    --rule: #555555;
    --ring: #efefef;
  }
  * { margin: 0; padding: 0; box-sizing: border-box; }
  html, body { width: 1200px; height: 1200px; overflow: hidden; }
  body { background: var(--backdrop); position: relative; font-family: "Outfit", sans-serif; color: var(--ink); }

  .card-spread {
    position: absolute; left: 55px; top: 260px; width: 1096px; height: 685px;
    background: var(--card); overflow: hidden;
  }
  .rings { position: absolute; inset: 0; }
  .fold-line { position: absolute; left: 546px; top: 4px; bottom: 0; width: 1px; background: var(--rule); }

  .warranty-panel { position: absolute; left: 0; top: 0; width: 546px; height: 100%; }
  .warranty-title {
    position: absolute; top: 55px; left: 0; width: 546px; text-align: center;
    font-weight: 300; font-size: 31px; letter-spacing: 0.5px;
  }
  .warranty-fields { position: absolute; left: 30px; top: 159px; width: 473px; list-style: none; border-top: 1px solid var(--rule); }
  .warranty-fields li {
    height: 69.6px; border-bottom: 1px solid var(--rule);
    font-weight: 300; font-size: 25px; padding: 18px 0 0 2px;
  }
  .contact-block {
    position: absolute; top: 578px; left: 0; width: 546px; text-align: center;
    font-weight: 300; font-size: 18.5px; line-height: 25px;
  }
  .contact-block .divider { margin: 0 12px; }

  .cover-panel { position: absolute; left: 547px; top: 0; right: 0; height: 100%; }
  .brand { position: absolute; left: 0; top: 262px; width: 100%; text-align: center; }
  .brand-name {
    font-weight: 300; font-size: 32px; letter-spacing: 4px;
    text-transform: uppercase; white-space: nowrap;
  }
  .brand-motto {
    font-weight: 300; font-size: 15px; letter-spacing: 2.5px;
    text-transform: uppercase; white-space: nowrap; margin-top: 22px;
  }
  .cover-title {
    position: absolute; top: 590px; left: 0; width: 100%; text-align: center;
    font-weight: 300; font-size: 32px;
  }
</style>
</head>
<body>
  <div class="card-spread">
    <svg class="rings" width="1096" height="685" viewBox="0 0 1096 685" aria-hidden="true">
      <circle cx="1096" cy="26" r="188" fill="none" stroke="var(--ring)" stroke-width="28"/>
      <circle cx="547" cy="662" r="188" fill="none" stroke="var(--ring)" stroke-width="28"/>
    </svg>
    <div class="fold-line"></div>

    <section class="warranty-panel">
      <h2 class="warranty-title">WARRANTY INFORMATION</h2>
      <ul class="warranty-fields">
        <li>Name</li>
        <li>Model</li>
        <li>Seriel Number</li>
        <li>Dial</li>
        <li>Date of purchase</li>
      </ul>
      <p class="contact-block">
        www.courtofmaywell.com<span class="divider">|</span>(+31) 612048395<br>
        Havenkade 27, 3011 TL Rotterdam, Netherlands
      </p>
    </section>

    <section class="cover-panel">
      <div class="brand">
        <h1 class="brand-name">Court of Maywell</h1>
        <p class="brand-motto">Kept with care, worn for life</p>
      </div>
      <h2 class="cover-title">GUARANTEE CARD</h2>
    </section>
  </div>
</body>
</html>
```